Auntie Verdict Billboard

I need a billboard designed for a Personal Injury Law firm. I need to simple not busy. I am attaching the following as suggestions to use. Need good colors that show up from Road Simple that can leave people associating injury lawyer with Auntie Verdict. Big picture of Dottie. Need Auntieverdict.com and 555-417-9038 to be big. possiblly let the emojis do the talking for personal injury and money settlement. Colors for logo should be similar to website auntieverdict.com
Updates

Billboard size. 10.5ft. X 36ft.

Target Market(s)

Car Accident Victims

Font styles to use
Sans Serif

Requirements
Must have
• Picture of Dottie. auntieverdict.com. 555-417-9038. message needs to be clear that she is a personal injury attorney. Clear simple message. Colors bold and visable to highway drivers
Should not have
• Busy ad.

```html
<!DOCTYPE html>
<html lang="en">
<head>
<meta charset="utf-8">
<title>Auntie Verdict Billboard</title>
<link href="https://fonts.googleapis.com/css2?family=Archivo+Black&family=Lato:wght@400;700&family=Open+Sans:wght@700;800&display=swap" rel="stylesheet">
<style>
  :root {
    --page: #e6e7ea;
    --board: #ffffff;
    --red: #c11f2e;
    --blue: #0b559c;
    --navy: #1b2130;
    --white: #ffffff;
    --suit: #1c2230;
    --hair: #16161a;
    --tone: #cfa08c;
    --sun: #f6c21c;
  }
  html, body {
    margin: 0;
    width: 1200px;
    height: 960px;
    overflow: hidden;
    background: var(--page);
  }
  .billboard {
    position: absolute;
    left: 40px;
    top: 316px;
    width: 1120px;
    height: 328px;
    background: var(--board);
    box-shadow: 0 18px 30px rgba(0,0,0,0.25);
    overflow: hidden;
  }
  .attorney-photo {
    position: absolute;
    left: 76px;
    top: 8px;
    width: 262px;
    height: 320px;
    z-index: 2;
    background: linear-gradient(to bottom, var(--hair) 0%, #3a2f2c 30%, var(--tone) 42%, var(--suit) 62%, var(--suit) 100%);
    border-radius: 110px 110px 0 0;
  }
  .firm-name {
    position: absolute;
    left: 400px;
    top: 72px;
    width: 440px;
    display: flex;
    align-items: center;
    justify-content: center;
    gap: 12px;
    font-family: "Lato", sans-serif;
    font-weight: 700;
    font-size: 28px;
    letter-spacing: 2px;
    color: var(--navy);
    white-space: nowrap;
  }
  .firm-name .mark {
    width: 18px;
    height: 18px;
    background: var(--navy);
    flex: none;
  }
  .injury-emoji {
    position: absolute;
    left: 850px;
    top: 22px;
    width: 116px;
    height: 116px;
    border-radius: 50%;
    background: radial-gradient(circle at 40% 35%, #ffe066, var(--sun) 60%, #e0a10f);
  }
  .headline {
    position: absolute;
    left: 350px;
    right: 20px;
    top: 148px;
    margin: 0;
    text-align: center;
    font-family: "Archivo Black", sans-serif;
    font-weight: 400;
    font-size: 72px;
    line-height: 1;
    color: var(--red);
    white-space: nowrap;
  }
  .contact-band {
    position: absolute;
    left: 330px;
    top: 244px;
    width: 790px;
    height: 84px;
    background: var(--blue);
    display: flex;
    align-items: center;
  }
  .phone {
    margin-left: 45px;
    font-family: "Open Sans", sans-serif;
    font-weight: 800;
    font-size: 60px;
    letter-spacing: -1px;
    color: var(--white);
    white-space: nowrap;
  }
  .divider {
    width: 1px;
    height: 44px;
    background: var(--white);
    margin: 0 26px;
    flex: none;
  }
  .website {
    font-family: "Lato", sans-serif;
    font-weight: 400;
    font-size: 13px;
    letter-spacing: 2.6px;
    color: var(--white);
    white-space: nowrap;
  }
  .website strong { font-weight: 700; }
</style>
</head>
<body>
  <section class="billboard">
    <div class="attorney-photo" role="img" aria-label="Portrait photo of the attorney in a dark suit"></div>
    <div class="firm-name"><span class="mark"></span>BIRCHWELL LAW GROUP</div>
    <div class="injury-emoji" role="img" aria-label="Injured emoji with a bandaged head"></div>
    <h1 class="headline">AUNTIE VERDICT</h1>
    <div class="contact-band">
      <span class="phone">555-417-9038</span>
      <span class="divider"></span>
      <span class="website">WWW.<strong>AUNTIEVERDICT</strong>.COM</span>
    </div>
  </section>
</body>
</html>
```